TA BRAMLEY BUSINESS CARD DESIGN PROJECT

We need to utilize our logo that was expertly created on PixelHarbor and now need to match this with a business card design.

```html
<!DOCTYPE html>
<html lang="en">
<head>
<meta charset="utf-8">
<title>TA Bramley – Business Card</title>
<link href="https://fonts.googleapis.com/css2?family=Open+Sans:wght@400;700&display=swap" rel="stylesheet">
<style>
  :root {
    --stage: #e8e5e1;
    --ink: #161719;
    --ink-soft: #232427;
    --paper: #ffffff;
    --brand-blue: #1556b0;
    --text-light: #f2f2f2;
  }
  * { box-sizing: border-box; margin: 0; padding: 0; }
  html, body {
    width: 1200px; height: 834px; overflow: hidden;
    background: var(--stage);
    font-family: "Open Sans", Arial, sans-serif;
  }
  .canvas {
    position: relative; width: 1200px; height: 834px;
  }
  .card {
    position: absolute; top: 262px;
    width: 540px; height: 309px;
    overflow: hidden;
    box-shadow: 0 10px 28px rgba(0,0,0,.22);
  }
  .card--front { left: 50px; background: var(--ink); }
  .card--back  { left: 610px; background: var(--ink); }

  .front-art { position: absolute; inset: 0; }

  .holder {
    position: absolute; left: 30px; top: 96px;
  }
  .holder__name {
    color: var(--brand-blue); font-weight: 700; font-size: 18px;
    letter-spacing: .5px; line-height: 1.2;
  }
  .holder__title {
    color: var(--text-light); font-size: 14px; line-height: 1.3;
  }
  .contacts {
    list-style: none; position: absolute; left: 30px; top: 160px;
    color: var(--text-light); font-size: 13px;
  }
  .contacts li {
    display: flex; align-items: center; gap: 8px; height: 22px;
  }
  .contacts svg { width: 12px; height: 12px; fill: var(--brand-blue); flex: none; }

  .address {
    position: absolute; right: 26px; bottom: 20px;
    color: var(--text-light); font-size: 14px; line-height: 1.55;
    font-style: normal; text-align: right;
  }

  .brand-name {
    position: absolute; color: var(--brand-blue);
    font-weight: 700; font-size: 34px; letter-spacing: 2px; white-space: nowrap;
  }
  .card--front .brand-name { left: 270px; top: 92px; }

  .back-pattern {
    position: absolute; inset: 0;
    background: radial-gradient(ellipse at 35% 30%, #2c2d30 0%, var(--ink-soft) 45%, var(--ink) 100%);
  }
  .card--back .brand-name {
    left: 50%; top: 50%; transform: translate(-50%, -50%); font-size: 30px;
  }
</style>
</head>
<body>
<main class="canvas">

  <section class="card card--front" aria-label="Business card front">
    <svg class="front-art" viewBox="0 0 540 309" aria-hidden="true">
      <path fill="var(--paper)" d="M0,0 H540 V228 C400,220 280,215 240,165 C200,110 130,55 0,55 Z"/>
      <path fill="none" stroke="var(--brand-blue)" stroke-width="3" d="M0,47 C128,47 196,100 233,152"/>
      <path fill="none" stroke="var(--brand-blue)" stroke-width="3" d="M330,205 C400,215 470,218 540,219"/>
    </svg>

    <div class="brand-name">TA BRAMLEY</div>

    <div class="holder">
      <p class="holder__name">MARCUS HALE</p>
      <p class="holder__title">Managing Director</p>
    </div>

    <ul class="contacts">
      <li>
        <svg viewBox="0 0 24 24"><path d="M6.6 10.8a15.1 15.1 0 0 0 6.6 6.6l2.2-2.2a1 1 0 0 1 1-.25 11.4 11.4 0 0 0 3.6.57 1 1 0 0 1 1 1V20a1 1 0 0 1-1 1A17 17 0 0 1 3 4a1 1 0 0 1 1-1h3.5a1 1 0 0 1 1 1c0 1.25.2 2.45.57 3.6a1 1 0 0 1-.25 1z"/></svg>
        <span>5550142876</span>
      </li>
      <li>
        <svg viewBox="0 0 24 24"><path d="M7 1h10a2 2 0 0 1 2 2v18a2 2 0 0 1-2 2H7a2 2 0 0 1-2-2V3a2 2 0 0 1 2-2zm0 3v14h10V4z"/></svg>
        <span>5550198234</span>
      </li>
      <li>
        <svg viewBox="0 0 24 24"><path d="M2 5h20v14H2zm2 2v.5l8 5 8-5V7z"/></svg>
        <span>info@tabramley.com</span>
      </li>
      <li>
        <svg viewBox="0 0 24 24"><path d="M12 2a10 10 0 1 0 0 20 10 10 0 0 0 0-20zm6.9 6h-3a15.7 15.7 0 0 0-1.4-3.6A8 8 0 0 1 18.9 8zM12 4a14 14 0 0 1 1.9 4h-3.8A14 14 0 0 1 12 4zM4.3 14a8 8 0 0 1 0-4h3.4a16 16 0 0 0 0 4zm.8 2h3a15.7 15.7 0 0 0 1.4 3.6A8 8 0 0 1 5.1 16zm3-8h-3a8 8 0 0 1 4.4-3.6A15.7 15.7 0 0 0 8.1 8zM12 20a14 14 0 0 1-1.9-4h3.8A14 14 0 0 1 12 20zm2.3-6H9.7a14.7 14.7 0 0 1 0-4h4.6a14.7 14.7 0 0 1 0 4zm.2 5.6a15.7 15.7 0 0 0 1.4-3.6h3a8 8 0 0 1-4.4 3.6zm1.8-5.6a16 16 0 0 0 0-4h3.4a8 8 0 0 1 0 4z"/></svg>
        <span>www.yourwebsite.com</span>
      </li>
    </ul>

    <address class="address">
      Your address, City<br>State, Zip 1234
    </address>
  </section>

  <section class="card card--back" aria-label="Business card back">
    <div class="back-pattern" role="img" aria-label="Dark embossed repeating brand pattern covering the card back"></div>
    <div class="brand-name">TA BRAMLEY</div>
  </section>

</main>
</body>
</html>
```